Lark Vista Perks Needs a Website Design

We need a website design for a new service we are starting. Users enter a coupon in a redemption page and either create an account or sign in. they can then use the credits they accumulate from the coupons to purchase items listed on the site.

we need a design for the following:
-the coupon redemption page (with a choice to either sign in or create an account)
-a product listing page (with search filters and a search bar. the search bar can be displayed in the header of the site)
-a product detail page, showing the product's title, image, credit redemption value, brand and any category associated with the item
-a my account page, with:
*a list of the pluses (coupons/credit added to account) and the minuses (orders placed/credits subtracted from account) to show a detailed description of their history on the site)
*an area for users to edit their name, phone number, address etc
*an area for users to add / edit their casino membership number and casino
*an area for users to add a coupon to their account
-a cart / checkout process:
*cart displaying items and their total
*entering / selecting an address from their account
*review order details page where they can submit their order (and warning the user that doing so will subtract the required credits from their account)

remember that no ecommerce or money is used on the site.. users are spending their credits and checkout their cart with the credits they accumulated, so the items each have a credit redemption value and the checkout process is shown in credits.

we are not very particular with any design preference, other than we'd like it to be predominately white.

If designing the site with css please make sure to use bootstrap in your designs. thanks!

Target Market(s)

adults 45-65

Industry/Entity Type

Casino

Coding

Coded - Design and coding required

Number of Pages Required

5+ page

Font styles to use
Sans Serif

Requirements
Must have
• css must use with bootstrap
Nice to have
• simplified, easy interface. we are targeting an older crowd and dont want to confuse them
Should not have
• the site shouldnt have any dollar values. all product prices, checkout totals and user accrual's (in the my account page) should be in credits

```html
<!DOCTYPE html>
<html lang="en">
<head>
<meta charset="utf-8">
<title>Lark Vista Perks — Coupon Rewards</title>
<link href="https://fonts.googleapis.com/css2?family=Montserrat:wght@500;600;700&family=Open+Sans:wght@400;600;700&display=swap" rel="stylesheet">
<style>
:root{
  --blue:#1f6fc5;
  --blue-dark:#1557a3;
  --ink:#222629;
  --text:#555b61;
  --muted:#8a9096;
  --line:#dfe3e8;
  --panel:#f1f3f6;
  --footer:#f5f6f8;
  --white:#ffffff;
  --hero-a:#dcc6ab;
  --hero-b:#c6a887;
  --star:#c9ced3;
}
*{box-sizing:border-box;margin:0;padding:0}
html,body{width:1200px;height:2540px;overflow:hidden}
body{font-family:"Open Sans",Arial,sans-serif;color:var(--text);background:var(--white);position:relative}
.section{position:absolute;left:0;width:1200px}
h2.section-title{font-family:"Montserrat",Arial,sans-serif;font-weight:700;color:var(--ink);font-size:26px;letter-spacing:1px;text-align:center;text-transform:uppercase}

/* header */
.site-header{top:0;height:80px;display:flex;align-items:center;padding:0 60px;justify-content:space-between}
.brand{font-family:"Montserrat",Arial,sans-serif;font-weight:700;font-size:26px;color:var(--ink);letter-spacing:.5px}
.main-nav{display:flex;align-items:center;gap:28px;font-family:"Montserrat",Arial,sans-serif;font-size:12px;font-weight:600;color:var(--ink);letter-spacing:.5px}
.btn-signup{border:2px solid var(--blue);color:var(--blue);padding:6px 14px;border-radius:2px}

/* hero */
.hero{top:80px;height:492px;background:linear-gradient(90deg,var(--hero-a),var(--hero-b))}
.hero-photo{position:absolute;left:0;top:0;width:560px;height:492px;background:linear-gradient(135deg,#d6bfa2 0%,#5bb8c9 40%,#e2a040 70%,#c9ad8c 100%);opacity:.85}
.hero-copy{position:absolute;left:640px;top:150px;color:var(--white)}
.hero-copy h1{font-family:"Montserrat",Arial,sans-serif;font-size:46px;font-weight:700;letter-spacing:2px}
.hero-copy p{font-size:18px;margin-top:10px}
.btn-outline{display:inline-block;margin-top:44px;border:2px solid var(--ink);color:var(--ink);font-size:15px;padding:9px 22px}

/* partners */
.earn{top:610px;height:250px}
.partner-row{position:absolute;top:90px;left:70px;display:flex;gap:40px}
.partner{width:180px;text-align:center}
.partner-box{height:90px;border:1px solid var(--line);display:flex;align-items:center;justify-content:center;gap:8px;font-family:"Open Sans",Arial,sans-serif;font-weight:700;font-size:20px;color:var(--ink)}
.partner-box i{width:14px;height:14px;background:var(--ink);display:block}
.shop-link{display:block;margin-top:14px;color:var(--blue);font-weight:600;font-size:15px}

/* products */
.products{top:880px;height:500px;background:var(--panel)}
.products h2.section-title{position:absolute;left:82px;top:60px;text-align:left;font-size:22px}
.options{position:absolute;right:82px;top:64px;display:flex;gap:16px;align-items:center;font-size:12px;color:var(--muted)}
.options span.ico{width:12px;height:10px;background:var(--ink);display:block}
.product-row{position:absolute;left:82px;top:130px;display:flex;gap:45px}
.product{width:225px}
.product-img{height:240px;background:var(--white);border:1px solid var(--line);display:flex;align-items:center;justify-content:center}
.product-img div{width:150px;height:130px;border-radius:8px}
.actions{display:flex;gap:6px;margin-top:10px;height:26px}
.actions span{width:26px;height:26px;border:1px solid var(--line);background:var(--white);display:flex;align-items:center;justify-content:center}
.product-name{margin-top:10px;font-size:14px;color:var(--text)}
.product-foot{display:flex;justify-content:space-between;align-items:center;margin-top:4px}
.price{font-family:"Montserrat",Arial,sans-serif;font-size:20px;font-weight:700;color:var(--blue);white-space:nowrap}
.price small{font-size:13px;font-weight:600;margin-left:3px}
.stars{color:var(--star);font-size:12px;letter-spacing:2px}

/* categories */
.categories{top:1380px;height:300px;background:linear-gradient(120deg,var(--blue-dark),var(--blue) 55%,#2b7fd4)}
.categories h2.section-title{color:var(--white);position:absolute;top:70px;width:100%}
.cat-row{position:absolute;left:100px;top:128px;display:flex;gap:40px}
.cat{width:172px;height:120px;border:1px solid rgba(255,255,255,.55);display:flex;flex-direction:column;align-items:center;justify-content:center;gap:14px;color:var(--white);font-size:14px}

/* blog */
.blog{top:1710px;height:420px}
.blog h2.section-title{position:absolute;top:30px;width:100%}
.post-row{position:absolute;left:70px;top:90px;display:flex;gap:35px}
.post{width:330px}
.post-img{height:160px}
.post h3{font-family:"Montserrat",Arial,sans-serif;font-size:15px;font-weight:700;color:var(--ink);margin-top:22px;text-transform:uppercase}
.post p{font-size:13px;line-height:1.6;margin-top:8px;color:var(--muted)}

/* footer */
.site-footer{top:2160px;height:280px;background:var(--footer)}
.foot-col{position:absolute;top:40px;width:230px}
.foot-col h4{font-family:"Montserrat",Arial,sans-serif;font-size:17px;font-weight:700;color:var(--ink);text-transform:uppercase;margin-bottom:14px}
.foot-col li{list-style:none;font-size:13px;color:var(--muted);line-height:26px}
.foot-col p{font-size:13px;color:var(--muted);line-height:1.6}
.news-input{margin-top:18px;height:38px;border:1px solid var(--line);background:var(--white);font-size:12px;color:var(--muted);padding:10px 12px}
.news-btn{margin-top:8px;height:38px;background:var(--blue);color:var(--white);font-weight:700;font-size:13px;text-align:center;line-height:38px}

.bottom-bar{top:2440px;height:100px;text-align:center}
.bottom-bar p{margin-top:22px;font-size:12px;color:var(--muted)}
.socials{display:flex;gap:10px;justify-content:center;margin-top:14px}
.socials span{width:26px;height:26px;border:1px solid #b7bdc3;border-radius:50%}
</style>
</head>
<body>

<header class="section site-header">
  <div class="brand">LARK VISTA PERKS</div>
  <nav class="main-nav">
    <span>HOME</span><span>ABOUT</span><span>EARN POINTS</span><span>REDEEM POINTS</span><span>MULTIPLE POINTS</span><span>CONTACT</span>
    <span class="btn-signup">SIGN UP</span>
  </nav>
</header>

<section class="section hero">
  <div class="hero-photo" role="img" aria-label="Shopper holding colourful shopping bags"></div>
  <div class="hero-copy">
    <h1>COUPON REWARDS</h1>
    <p>We are a coupon redemption company</p>
    <span class="btn-outline">Get Start Now</span>
  </div>
</section>

<section class="section earn">
  <h2 class="section-title">Earn Points on Online Shopping</h2>
  <div class="partner-row">
    <div class="partner"><div class="partner-box"><i></i>Fernwell</div><span class="shop-link">Shop Now</span></div>
    <div class="partner"><div class="partner-box">Quillory</div><span class="shop-link">Shop Now</span></div>
    <div class="partner"><div class="partner-box">Brisko</div><span class="shop-link">Shop Now</span></div>
    <div class="partner"><div class="partner-box">Tandemark</div><span class="shop-link">Shop Now</span></div>
    <div class="partner"><div class="partner-box">Holloway</div><span class="shop-link">Shop Now</span></div>
  </div>
</section>

<section class="section products">
  <h2 class="section-title">Products on Sales</h2>
  <div class="options">Options: <span class="ico"></span><span class="ico"></span><span class="ico"></span><span class="ico"></span><span class="ico"></span></div>
  <div class="product-row">
    <div class="product">
      <div class="product-img"><div role="img" aria-label="Black digital camera" style="background:linear-gradient(135deg,#3a3d40,#111)"></div></div>
      <div class="actions">
        <span><svg width="12" height="12" viewBox="0 0 12 12"><path d="M6 11 1.5 6.5a2.6 2.6 0 0 1 4.5-3 2.6 2.6 0 0 1 4.5 3z" fill="none" stroke="#555" stroke-width="1.2"/></svg></span>
        <span><svg width="12" height="12" viewBox="0 0 12 12"><path d="M1 2h2l1.5 6h5.5l1-4H4" fill="none" stroke="#555" stroke-width="1.2"/></svg></span>
        <span><svg width="12" height="12" viewBox="0 0 12 12"><ellipse cx="6" cy="6" rx="5" ry="3" fill="none" stroke="#555" stroke-width="1.2"/><circle cx="6" cy="6" r="1.3" fill="#555"/></svg></span>
        <span><svg width="12" height="12" viewBox="0 0 12 12"><path d="M2 4h8M2 8h8" stroke="#555" stroke-width="1.2"/></svg></span>
      </div>
      <div class="product-name">Finibus Bonorum Et Malorum</div>
      <div class="product-foot"><span class="price">125<small>Credits</small></span><span class="stars">★★★★★</span></div>
    </div>
    <div class="product">
      <div class="product-img"><div role="img" aria-label="White smartphone" style="width:80px;height:160px;background:linear-gradient(160deg,#e9ecef,#9fa7ae)"></div></div>
      <div class="actions"></div>
      <div class="product-name">Finibus Bonorum Et Malorum</div>
      <div class="product-foot"><span class="price">125<small>Credits</small></span><span class="stars">★★★★★</span></div>
    </div>
    <div class="product">
      <div class="product-img"><div role="img" aria-label="Yellow over-ear headphones" style="border-radius:50%;background:radial-gradient(circle,#f5c518,#2a2a2a)"></div></div>
      <div class="actions"></div>
      <div class="product-name">Finibus Bonorum Et Malorum</div>
      <div class="product-foot"><span class="price">125<small>Credits</small></span><span class="stars">★★★★★</span></div>
    </div>
    <div class="product">
      <div class="product-img"><div role="img" aria-label="Silver laptop" style="width:170px;height:110px;background:linear-gradient(160deg,#6fb2e6,#c7ccd1)"></div></div>
      <div class="actions"></div>
      <div class="product-name">Finibus Bonorum Et Malorum</div>
      <div class="product-foot"><span class="price">125<small>Credits</small></span><span class="stars">★★★★★</span></div>
    </div>
  </div>
</section>

<section class="section categories">
  <h2 class="section-title">Categories</h2>
  <div class="cat-row">
    <div class="cat"><svg width="34" height="30" viewBox="0 0 34 30"><path d="M17 2 2 15h4v13h8v-8h6v8h8V15h4z" fill="#fff"/></svg>Home and kitchen</div>
    <div class="cat"><svg width="32" height="32" viewBox="0 0 32 32"><circle cx="16" cy="16" r="13" fill="none" stroke="#fff" stroke-width="3"/><path d="M16 9v8l5 3" stroke="#fff" stroke-width="3" fill="none"/></svg>Watches</div>
    <div class="cat"><svg width="30" height="32" viewBox="0 0 30 32"><path d="M4 10h22l-2 20H6z" fill="#fff"/><path d="M10 10V6a5 5 0 0 1 10 0v4" stroke="#fff" stroke-width="2.5" fill="none"/></svg>Grocery</div>
    <div class="cat"><svg width="34" height="30" viewBox="0 0 34 30"><path d="M4 20v-5a13 13 0 0 1 26 0v5" stroke="#fff" stroke-width="3" fill="none"/><rect x="2" y="18" width="8" height="11" rx="2" fill="#fff"/><rect x="24" y="18" width="8" height="11" rx="2" fill="#fff"/></svg>Music</div>
    <div class="cat"><svg width="36" height="30" viewBox="0 0 36 30"><rect x="2" y="2" width="32" height="20" rx="2" fill="none" stroke="#fff" stroke-width="3"/><path d="M12 28h12M18 22v6" stroke="#fff" stroke-width="3"/></svg>Desktop</div>
  </div>
</section>

<section class="section blog">
  <h2 class="section-title">Our Blog Post</h2>
  <div class="post-row">
    <article class="post">
      <div class="post-img" role="img" aria-label="Shopper browsing a shoe display" style="background:linear-gradient(120deg,#f2f2f2,#b88a6a 60%,#e6e0da)"></div>
      <h3>Sed perspiciatis unde omnis</h3>
      <p>Lorem ipsum dolor sit amet, consectetur adipiscing elit, sed do eiusmod tempor incididunt ut labore et dolore magna aliqua veniam.</p>
    </article>
    <article class="post">
      <div class="post-img" role="img" aria-label="Group of friends holding shopping bags" style="background:linear-gradient(120deg,#3f86c7,#d89a6a 55%,#e9d4b8)"></div>
      <h3>Sed perspiciatis unde omnis</h3>
      <p>Lorem ipsum dolor sit amet, consectetur adipiscing elit, sed do eiusmod tempor incididunt ut labore et dolore magna aliqua veniam.</p>
    </article>
    <article class="post">
      <div class="post-img" role="img" aria-label="Shoppers with bags in a bright mall" style="background:linear-gradient(120deg,#f2c7c9,#d84b78 50%,#f3e6e0)"></div>
      <h3>Sed perspiciatis unde omnis</h3>
      <p>Lorem ipsum dolor sit amet, consectetur adipiscing elit, sed do eiusmod tempor incididunt ut labore et dolore magna aliqua veniam.</p>
    </article>
  </div>
</section>

<footer class="section site-footer">
  <div class="foot-col" style="left:90px"><h4>About Us</h4><ul><li>About us</li><li>Shipping Guide</li><li>Delivery Information</li><li>Privacy Policy</li><li>Sitemap</li></ul></div>
  <div class="foot-col" style="left:350px"><h4>My Account</h4><ul><li>My Order</li><li>Order History</li><li>Wish List</li><li>Newsletter</li><li>Contact Us</li></ul></div>
  <div class="foot-col" style="left:610px"><h4>Catalog</h4><ul><li>New Arrival</li><li>Best Seller</li><li>Discounted Products</li><li>Specials</li><li>Gift Card</li></ul></div>
  <div class="foot-col" style="left:870px;width:240px"><h4>Newsletter</h4>
    <p>Sign up to receive the latest offers and reward news first.</p>
    <div class="news-input">Enter your email</div>
    <div class="news-btn">SUBSCRIBE NOW</div>
  </div>
</footer>

<div class="section bottom-bar">
  <p>Copyright © 2017 Lark Vista Perks. All Rights Reserved.</p>
  <div class="socials"><span></span><span></span><span></span><span></span><span></span></div>
</div>

</body>
</html>
```